Velk Partners Building Business Cards

We need a business card that reflects our business as "Solar Experts" in San Diego. Browse our website www.velkpartners.example our License needs to be displayed as "CSLB# 3867140" our phone number is (619) 555-0187

Save thousands on your electric bills and increase the value of your home while helping to protect the environment. Our solar installation experts will help you design the system that's right for you, using only the highest quality equipment that will look great and give you ideal performance. Our goal is to make you energy independent, and get your electric bill to 0.

Paul Osterby
(619) 555-0187
paul@velkpartners.example

Target Market(s)

Home owners in san diego looking for solar

Industry/Entity Type

Solar Energy

Contact Information for Business Card

Paul Osterby
(619) 555-0187
paul@velkpartners.example

Font styles to use
Other font styles liked:
• Use our logo font

Requirements
Must have
• License needs to be displayed as "CSLB# 3867140" our phone number is (619) 555-0187
Nice to have
• Real images of rooftop home solar in san diego
Should not have
• our business address

```html
<!DOCTYPE html>
<html lang="en">
<head>
<meta charset="utf-8">
<title>Velk Partners Building — Business Cards</title>
<link href="https://fonts.googleapis.com/css2?family=Open+Sans:wght@400;700;800&family=Oswald:wght@600&display=swap" rel="stylesheet">
<style>
  :root{
    --navy:#1f4b8a;
    --sun:#f5a81c;
    --paper:#ffffff;
    --ink:#2f3440;
    --stage:#2a2d31;
  }
  *{box-sizing:border-box;margin:0;padding:0}
  html,body{width:1200px;height:900px;overflow:hidden;background:var(--stage)}
  .canvas{position:relative;width:1200px;height:900px}
  .card{position:absolute;left:340px;width:520px;height:297px;border-radius:14px;overflow:hidden}
  .card--front{top:120px;background:var(--paper)}
  .card--back{top:480px;background:var(--navy)}
  .card__art{position:absolute;inset:0;width:100%;height:100%}

  .holder{position:absolute;left:34px;top:100px;font-family:"Oswald",sans-serif;font-weight:600;font-size:28px;line-height:36px;letter-spacing:.5px;text-transform:uppercase}
  .holder__first{color:var(--navy)}
  .holder__last{color:var(--sun)}
  .contact{position:absolute;left:34px;top:148px;font-family:"Open Sans",sans-serif;font-size:12.5px;color:var(--ink);line-height:21px}
  .contact__row{display:flex;align-items:center;gap:8px}
  .contact__row svg{width:13px;height:13px;flex:none}

  .brand{font-family:"Open Sans",sans-serif;font-weight:800;letter-spacing:-.5px;line-height:1.05}
  .brand--front{position:absolute;right:30px;top:52px;width:240px;text-align:right;font-size:30px;color:var(--navy)}
  .license{position:absolute;right:30px;top:234px;font-family:"Open Sans",sans-serif;font-size:12.5px;line-height:17px;color:var(--ink)}
  .site{font-family:"Open Sans",sans-serif;font-size:14px;color:var(--paper)}
  .site__mid{color:var(--sun)}
  .site--front{position:absolute;right:30px;top:272px;line-height:18px}

  .brand--back{position:absolute;left:0;right:0;top:78px;text-align:center;font-size:44px;color:var(--paper)}
  .site--back{position:absolute;left:0;right:0;top:222px;text-align:center;font-size:15px}
</style>
</head>
<body>
<main class="canvas">

  <section class="card card--front" aria-label="Business card front">
    <svg class="card__art" viewBox="0 0 520 297" aria-hidden="true">
      <path d="M0,244 C110,248 190,262 240,268 L520,268 L520,297 L0,297 Z" fill="var(--navy)"/>
      <path d="M0,230 C100,234 170,248 215,262 C165,254 95,246 0,244 Z" fill="var(--sun)"/>
      <path d="M0,222 C120,226 200,244 245,258 L520,258" fill="none" stroke="var(--navy)" stroke-width="1.6"/>
    </svg>

    <h1 class="holder"><span class="holder__first">Paul</span> <span class="holder__last">Osterby</span></h1>
    <div class="contact">
      <p class="contact__row">
        <svg viewBox="0 0 24 24"><path fill="var(--navy)" d="M6.6 10.8a15.1 15.1 0 0 0 6.6 6.6l2.2-2.2a1 1 0 0 1 1-.25 11.4 11.4 0 0 0 3.6.57 1 1 0 0 1 1 1V20a1 1 0 0 1-1 1A17 17 0 0 1 3 4a1 1 0 0 1 1-1h3.5a1 1 0 0 1 1 1c0 1.25.2 2.45.57 3.57a1 1 0 0 1-.25 1z"/></svg>
        (619) 555-0187
      </p>
      <p class="contact__row">
        <svg viewBox="0 0 24 24"><rect x="3" y="5" width="18" height="14" rx="1.5" fill="none" stroke="var(--navy)" stroke-width="2"/><path d="M3.5 6l8.5 7 8.5-7" fill="none" stroke="var(--navy)" stroke-width="2"/></svg>
        paul@velkpartners.example
      </p>
    </div>

    <p class="brand brand--front">Velk Partners Building</p>
    <p class="license">License: CSLB# 3867140</p>
    <p class="site site--front">www.<span class="site__mid">velkpartners</span>.example</p>
  </section>

  <section class="card card--back" aria-label="Business card back">
    <p class="brand brand--back">Velk Partners<br>Building</p>
    <p class="site site--back">www.<span class="site__mid">velkpartners</span>.example</p>
  </section>

</main>
</body>
</html>
```